Beauty Therapy Web Design

I need a web page design for a small beauty therapy clinic, the owner is currently the only beauty therapist working there.
We require the following pages:
Home
About
Treatments
Nails
Courses
Contact
I will attach the clinics business card, treatment menu and signage so that you get a feeling for the branding colours etc.
This is the first website for the beauty therapist, she would like to attract new clients and also tourists that come in on the cruise ships. The thing that sets her apart from other clinics is that she welcomes texting for appointments.
I have selected refundable because I have never done this before so I don't know what to expect, I have the full intention of going through with it as long as I get a good design.
Feel free to ask for further information
Reason: Project extended as I am away for work and am unable to meet with the owner.
Target Market(s)
Females 18 to 50
Industry/Entity Type
Business
Look and feel

```html
<!DOCTYPE html>
<html lang="en">
<head>
<meta charset="utf-8">
<title>Lumara Beauty Therapy</title>
<link href="https://fonts.googleapis.com/css2?family=Arimo:wght@400;700&display=swap" rel="stylesheet">
<style>
:root{
  --purple:#4a2bb0;
  --purple-dark:#3c1f9a;
  --purple-light:#6a4ad0;
  --ink:#2e2560;
  --ink-soft:#3a2f70;
  --green:#0a8a2a;
  --green-dark:#066b1f;
  --green-light:#12a83a;
  --label-green:#0b7a25;
  --white:#ffffff;
  --rule:#ececf2;
  --footer-top:#f1f0f7;
}
*{margin:0;padding:0;box-sizing:border-box}
html,body{width:1005px;height:1200px;overflow:hidden;background:var(--white)}
body{font-family:"Arimo",Arial,sans-serif;color:var(--ink);position:relative}
.site-header{position:absolute;left:0;top:0;width:1005px;height:164px}
.brand{position:absolute;left:102px;top:28px;color:var(--purple);font-weight:700}
.brand-name{display:block;font-size:78px;line-height:82px;letter-spacing:-1px}
.brand-tag{display:block;font-size:34px;line-height:40px;letter-spacing:1px}
.contact-lines{position:absolute;right:91px;top:52px;text-align:right;font-size:13px;color:var(--ink-soft);line-height:24px}
.contact-lines .num{font-size:16px}
.address-line{position:absolute;right:91px;top:135px;font-size:13px;color:var(--ink-soft)}
.main-nav{position:absolute;left:41px;top:164px;width:939px;height:43px;border-radius:0 0 16px 16px;
  background:linear-gradient(90deg,var(--purple-dark),var(--purple-light) 45%,var(--purple-dark));}
.main-nav ul{list-style:none;display:flex;justify-content:center;height:100%;align-items:center;padding-left:6px}
.main-nav li{color:var(--white);font-size:12px;font-weight:700;padding:0 30px;border-left:1px solid rgba(255,255,255,.75);line-height:16px}
.main-nav li:last-child{border-right:1px solid rgba(255,255,255,.75)}
.hero-photo{position:absolute;left:41px;top:207px;width:379px;height:657px;
  background:radial-gradient(ellipse 30% 48% at 55% 52%,#e8b898,#f3d8c6 60%,#ffffff 100%)}
.feature{position:absolute;left:420px;top:207px;width:560px;height:317px;border-left:1px solid var(--rule);padding:26px 0 0 38px}
.feature h1{font-size:30px;font-weight:700;color:var(--ink);margin-bottom:26px}
.lead{font-size:14px;font-weight:700;line-height:20px;margin-bottom:27px;color:#24184f}
.body-text{font-size:14px;line-height:25px;width:420px;color:#24184f}
.btn{display:block;width:200px;height:40px;border-radius:20px;color:var(--white);font-size:20px;font-weight:700;
  text-align:center;line-height:40px;text-shadow:0 1px 2px rgba(0,0,0,.45)}
.btn-purple{background:linear-gradient(180deg,var(--purple-light),var(--purple-dark))}
.btn-green{background:linear-gradient(180deg,var(--green-light),var(--green-dark))}
.feature .btn{margin-top:35px;border:1px solid #9a7fe6}
.promo{position:absolute;top:524px;width:280px;height:340px;padding:32px 0 0 40px;color:var(--white)}
.promo-wax{left:420px;background:radial-gradient(ellipse at 60% 55%,#6447cf,var(--purple-dark) 80%)}
.promo-brazilian{left:700px;background:radial-gradient(ellipse at 60% 55%,#17b03e,var(--green-dark) 85%)}
.promo h2{font-size:20px;font-weight:700;margin-bottom:26px}
.promo .lead,.promo .body-text{color:var(--white);width:220px}
.promo .lead{line-height:25px;margin-bottom:22px}
.promo .btn{position:absolute;left:39px;top:258px}
.services{position:absolute;left:41px;top:904px;width:939px;height:90px}
.service{position:absolute;top:0;width:220px;height:90px;border:10px solid var(--purple);background:var(--white);display:flex;align-items:center}
.service-thumb{width:56px;height:70px;flex:none;margin-right:6px}
.service-label{color:var(--label-green);font-size:14px;font-weight:700;line-height:16px}
.thumb-eyes{background:linear-gradient(135deg,#f2dccd,#d9a98c)}
.thumb-legs{background:linear-gradient(135deg,#fff,#f0cdb5)}
.thumb-massage{width:104px;background:linear-gradient(180deg,#f6e6d8,#d8a482)}
.thumb-facial{background:linear-gradient(135deg,#e9ecec,#9eb0ae)}
.site-footer{position:absolute;left:40px;top:1034px;width:940px;height:156px;
  background:linear-gradient(180deg,var(--footer-top),var(--white));text-align:center;padding-top:35px;font-size:13px;line-height:24px;color:#3a1f55}
.site-footer .gap{display:inline-block;width:12px}
</style>
</head>
<body>
<header class="site-header">
  <div class="brand"><span class="brand-name">Lumara</span><span class="brand-tag">BEAUTY THERAPY</span></div>
  <div class="contact-lines">
    <div>Phone Tessa <span class="num">07 555 0132</span></div>
    <div>Cellphone <span class="num">027 555 0198</span></div>
  </div>
  <div class="address-line">Cnr Kowhai St. &amp; Harbour Rd, Mount Harbourview</div>
</header>
<nav class="main-nav">
  <ul><li>HOME</li><li>ABOUT</li><li>TREATMENTS</li><li>NAILS</li><li>COURSES</li><li>CONTACT</li></ul>
</nav>
<div class="hero-photo" role="img" aria-label="Photo of two elegant manicured hands raised against white"></div>
<section class="feature">
  <h1>Spa Deluxe Manicure</h1>
  <p class="lead">Homero nostrum definitionem mea et, his no malis</p>
  <p class="body-text">Homero nostrum definitionem mea et, his no malis ullamcorper, cu tollit nostrum pri. Qui id nusquam docendi inimicus, tota iusto mea eu. Mea cu paulo mollis, ad nam vide inciderint</p>
  <span class="btn btn-purple">Read more</span>
</section>
<section class="promo promo-wax">
  <h2>G Wax</h2>
  <p class="lead">Homero nostrum definitionem mea et, his no malis</p>
  <p class="body-text">Homero nostrum definitionem mea et, his no malis ullamcorper, cu tollit nostrum pri. Qui id</p>
  <span class="btn btn-green">Read more</span>
</section>
<section class="promo promo-brazilian">
  <h2>Brazilian Waxing</h2>
  <p class="lead">Homero nostrum definitionem mea et, his no malis</p>
  <p class="body-text">Homero nostrum definitionem mea et, his no malis ullamcorper, cu tollit nostrum pri. Qui id</p>
  <span class="btn btn-purple">Read more</span>
</section>
<section class="services">
  <div class="service" style="left:0"><div class="service-thumb thumb-eyes" role="img" aria-label="Photo of eyelash tinting treatment"></div><div class="service-label">Lash Tint &amp; Shape<br>BEAUTIFUL EYES</div></div>
  <div class="service" style="left:239px"><div class="service-thumb thumb-legs" role="img" aria-label="Photo of smooth waxed leg"></div><div class="service-label">Full &amp; Half Leg<br>WAXING</div></div>
  <div class="service" style="left:479px"><div class="service-thumb thumb-massage" role="img" aria-label="Photo of relaxing back massage"></div><div class="service-label">1/2 or 1 Hour<br>MASSAGE</div></div>
  <div class="service" style="left:719px"><div class="service-thumb thumb-facial" role="img" aria-label="Photo of purifying clay face mask"></div><div class="service-label">Purifying<br>FACIALS</div></div>
</section>
<footer class="site-footer">
  <div>Copyright 2012 Lumara Beauty Therapy</div>
  <div>Phone Tessa 07 555 0132<span class="gap"></span>Cellphone 027 555 0198</div>
  <div>Cnr Kowhai St. &amp; Harbour Rd, Mount Harbourview</div>
</footer>
</body>
</html>
```